Business Card Design For Office Furniture Clearance Company

Kestrel Office Clearance - our company name pretty much explains what we do, we clear offices for high end clients, mainly plc's and large international companies.

We require a nice looking business card that displays professionalism but without being too serious.

It would be nice to see just a little more than a conventional boring business card, make sure you add some flare.

Industry/Entity Type

Office Furniture

Contact Information for Business Card

CARD 1

Mark Holloway
Director
mark@kestrelofficeclearance.co.uk
m: 07700 153928

t: 01632 960418
www.kestrelofficeclearance.co.uk

Kestrel Office Clearance
Unit K4 B
2-8 Fenwick Lane
Bletchley
Milton Keynes
ZZ9 4QT

Clear offices, fresh starts… all at no cost to you.

CARD 2

Peter Radford
Director
peter@kestrelofficeclearance.co.uk
m: 07700 382615

t: 01632 960418

Kestrel Office Clearance
Unit K4 B
2-8 Fenwick Lane
Bletchley
Milton Keynes
ZZ9 4QT

Font styles to use
Sans Serif

Requirements
Must have
• A white background - as we have a blue logo.
Nice to have
• Nice use of the logo - play around with this and dissect it.

```html
<!DOCTYPE html>
<html lang="en">
<head>
<meta charset="utf-8">
<title>Kestrel Office Clearance – Business Card</title>
<link href="https://fonts.googleapis.com/css2?family=Arimo:wght@400;700&display=swap" rel="stylesheet">
<style>
  :root {
    --brand-blue: #1b80c8;
    --swoosh-grey: #3d3d3f;
    --text-grey: #5a5a5c;
    --rule: #222222;
    --paper: #ffffff;
    --stage: #e9eaec;
  }
  * { margin: 0; padding: 0; box-sizing: border-box; }
  html, body {
    width: 1200px; height: 950px; overflow: hidden;
    background: var(--stage);
    font-family: "Arimo", Arial, sans-serif;
  }
  .card {
    position: absolute;
    left: 232px;
    width: 735px; height: 420px;
    box-shadow: 0 6px 18px rgba(0,0,0,0.18);
    overflow: hidden;
  }
  /* Back */
  .card-back { top: 30px; background: var(--brand-blue); }
  .back-mark {
    position: absolute; left: 50%; top: 150px;
    transform: translate(-50%, -50%);
    display: flex; align-items: center; gap: 18px;
  }
  .back-mark .disc {
    width: 150px; height: 150px; border-radius: 50%; background: var(--paper);
  }
  .back-mark .name {
    color: var(--paper); font-size: 28px; font-weight: 700; white-space: nowrap;
  }
  .tagline {
    position: absolute; left: 40px; bottom: 42px;
    color: var(--paper); font-size: 15px; letter-spacing: 0.4px;
  }
  /* Front */
  .card-front { top: 480px; background: var(--paper); }
  .swoosh { position: absolute; inset: 0; }
  .front-mark {
    position: absolute; right: 35px; top: 30px;
    display: flex; align-items: center; gap: 16px;
  }
  .front-mark .name {
    color: var(--brand-blue); font-size: 24px; font-weight: 700; white-space: nowrap;
  }
  .front-mark .disc {
    width: 115px; height: 115px; border-radius: 50%; background: var(--brand-blue);
  }
  .divider {
    position: absolute; left: 385px; right: 35px; top: 172px;
    border-top: 1.5px solid var(--rule);
  }
  .address {
    position: absolute; right: 35px; top: 186px;
    text-align: right; color: var(--text-grey);
    font-size: 16px; line-height: 21px; font-style: normal;
  }
  .address .company { color: var(--brand-blue); font-size: 16px; }
  .person { position: absolute; left: 160px; top: 262px; }
  .person .full-name {
    display: flex; align-items: flex-end; gap: 8px;
    color: var(--brand-blue); font-size: 22px; font-weight: 700;
  }
  .person .full-name::after {
    content: ""; width: 200px; border-top: 1.5px solid var(--rule); margin-bottom: 4px;
  }
  .person .role { color: #333; font-size: 15px; margin-top: 4px; }
  .contacts { list-style: none; margin-top: 10px; }
  .contacts li {
    display: flex; align-items: center; gap: 8px;
    color: var(--text-grey); font-size: 15px; line-height: 22px;
  }
  .contacts svg { width: 14px; height: 14px; fill: var(--swoosh-grey); flex: none; }
</style>
</head>
<body>

<section class="card card-back" aria-label="Business card back">
  <div class="back-mark">
    <span class="disc"></span>
    <span class="name">Kestrel Office Clearance</span>
  </div>
  <p class="tagline">Clear offices, fresh starts… all at no cost to you.</p>
</section>

<section class="card card-front" aria-label="Business card front">
  <svg class="swoosh" viewBox="0 0 735 420" preserveAspectRatio="none" aria-hidden="true">
    <path d="M0 0 H345 C215 70 85 200 0 320 Z" fill="var(--brand-blue)"/>
    <path d="M345 0 C200 80 70 220 0 352 L0 326 C85 206 215 74 345 0 Z" fill="var(--swoosh-grey)"/>
    <path d="M345 0 C215 72 85 202 0 323" fill="none" stroke="var(--paper)" stroke-width="4"/>
  </svg>

  <div class="front-mark">
    <span class="name">Kestrel</span>
    <span class="disc"></span>
  </div>
  <div class="divider"></div>

  <address class="address">
    <div class="company">Kestrel Office Clearance</div>
    <div>Unit K4 B, 2-8 Fenwick Lane</div>
    <div>Harwick, Northfield</div>
    <div>ZZ9 4QT</div>
  </address>

  <div class="person">
    <div class="full-name">Mark Holloway</div>
    <div class="role">Director</div>
    <ul class="contacts">
      <li><svg viewBox="0 0 16 16"><path d="M3 1h3l1.5 4-2 1.3a9 9 0 0 0 4.2 4.2L11 8.5l4 1.5v3a2 2 0 0 1-2 2A12 12 0 0 1 1 3a2 2 0 0 1 2-2z"/></svg>01632 960418</li>
      <li><svg viewBox="0 0 16 16"><path d="M4 0h8a1 1 0 0 1 1 1v14a1 1 0 0 1-1 1H4a1 1 0 0 1-1-1V1a1 1 0 0 1 1-1zm1 2v10h6V2zm3 11a1 1 0 1 0 0 2 1 1 0 0 0 0-2z"/></svg>07700 153928</li>
      <li><svg viewBox="0 0 16 16"><path d="M0 3h16v1L8 9 0 4zm0 3 8 5 8-5v7H0z"/></svg>mark@kestrelofficeclearance.co.uk</li>
      <li><svg viewBox="0 0 16 16"><path d="M8 0a8 8 0 1 0 0 16A8 8 0 0 0 8 0zm0 2c.8 0 1.8 1.6 2.2 5H5.8C6.2 3.6 7.2 2 8 2zM2.1 7h2.2c.1-1.8.5-3.3 1-4.3A6 6 0 0 0 2.1 7zm9.6 0h2.2a6 6 0 0 0-3.2-4.3c.5 1 .9 2.5 1 4.3zM2.1 9a6 6 0 0 0 3.2 4.3c-.5-1-.9-2.5-1-4.3zm3.7 0c.4 3.4 1.4 5 2.2 5s1.8-1.6 2.2-5zm5.9 0c-.1 1.8-.5 3.3-1 4.3A6 6 0 0 0 13.9 9z"/></svg>www.kestrelofficeclearance.co.uk</li>
    </ul>
  </div>
</section>

</body>
</html>
```